We need UI/UX design for a public, informational website for The Copper Lantern.
The pages, structure, and content scope are already defined. Designers are required to work only on the UI/UX layout of these existing pages, focusing on clarity, hierarchy, spacing, and usability. Do not add, remove, rename, or reinterpret pages or content.
The website is strictly informational only. It must not include accounts, onboarding, payments, custody, escrow administration, marketplaces, dashboards, or any transactional functionality.
Scope of work
Apply UI/UX design to the predefined website pages
Design layout for text, images, notices, and sections
Ensure consistent components and layout patterns across page types
Optimize layouts for long form, compliance focused content
Content writing, page creation, and branding changes are out of scope.
Structure reference
The complete page list, hierarchy, and content definitions are provided in the technical documentation and must be treated as the primary source of truth.
A Figma link is provided only as a light visual reference for page existence and structure:
https://meadow-knot-48203956.plumsite.example/
Designers must rely on the documentation for in depth and authoritative reference.
Brand guidelines
The Copper Lantern has existing brand guidelines and official logos, including light and dark versions. These assets will be provided and must be followed exactly. Designers must not redesign, alter, or reinterpret the brand identity.
Look and feel direction
The desired visual direction is inspired by:
https://ledgerwaltz.example/
This reference is provided only to indicate:
Institutional and enterprise tone
Clean, modern typography
Strong hierarchy and generous whitespace
Editorial, content first layouts
Do not copy branding, layouts, components, or assets from the reference site.
Hero section direction
The hero section should follow a similar structural approach to the hero used on https://ledgerwaltz.example/
, meaning:
Strong editorial framing
Clear headline hierarchy
Calm, institutional first impression
However, the background video must be Abu Dhabi focused, not generic or global. The video should visually reflect:
Abu Dhabi skyline or architectural language
Institutional, sovereign, long term infrastructure tone
Clean, slow, cinematic motion
No promotional, marketing, or lifestyle visuals
The hero must remain informational, restrained, and credible. No hype. No calls to invest. No implied participation.
Constraints
One global primary CTA only: “Continue to Halvemark” (external)
All other interactions must be informational
No visuals or language implying offers, investment, eligibility, or participation
Clear separation between informational content and any external operational platforms
Deliverables
High fidelity UI/UX designs created in Figma, covering:
Desktop layouts
Tablet layouts where relevant
Mobile layouts
Complete Figma file(s) including:
All designed pages defined in the technical documentation
A reusable component library (headers, footers, cards, notice panels, forms, CTAs, typography styles, spacing system)
Clearly defined layout grids, spacing rules, and text styles
Proper use of components and variants, not detached frames
Designs prepared for developer handoff, including:
Clear layer naming and structure
Auto layout where appropriate
Consistent use of styles and components
Responsive behavior demonstrated within Figma
Notes or annotations only where necessary for clarity
No prototypes, interactions, or motion design beyond basic layout states, unless explicitly requested. The focus is static UI/UX clarity, not animation.
A detailed technical specification document and official brand assets will be provided.
Any designs delivered outside Figma, that alter structure or content, or that ignore the defined constraints, boundaries, or tone will be rejected.

```html
<!DOCTYPE html>
<html lang="en">
<head>
<meta charset="utf-8">
<title>The Copper Lantern — Governance and Project Origination Framework</title>
<link href="https://fonts.googleapis.com/css2?family=Archivo:wght@500;700;800;900&family=Inter:wght@400;500;600;700&display=swap" rel="stylesheet">
<style>
:root{
  --blue:#46a8f8;
  --purple:#a46ef5;
  --cyan:#14c3e3;
  --ink:#111111;
  --navy:#0c1428;
  --grey-bg:#f4f4f5;
  --white:#ffffff;
  --grad:linear-gradient(90deg,#46a8f8,#a46ef5);
}
*{box-sizing:border-box;margin:0;padding:0}
html,body{width:1200px;height:5254px;overflow:hidden}
body{font-family:"Inter",sans-serif;color:var(--ink);background:var(--white);position:relative}
.abs{position:absolute}
.display{font-family:"Archivo",sans-serif;font-weight:900;letter-spacing:-1.5px;text-transform:uppercase;line-height:1}
.pill{display:inline-flex;align-items:center;justify-content:center;border-radius:30px;background:linear-gradient(90deg,#46a8f8,#7fa2f6);color:#fff;font-weight:600;font-size:12px}
.c-blue{color:var(--blue)}
.c-purple{color:var(--purple)}
section{position:absolute;left:0;width:1200px;overflow:hidden}

/* brand */
.brand{display:flex;align-items:center;gap:12px;color:#fff;font-family:"Inter",sans-serif;font-weight:600;font-size:14px;letter-spacing:.3px;white-space:nowrap}
.brand-dot{width:28px;height:28px;border-radius:50%;background:#fff;flex:0 0 auto}

/* hero */
.hero{top:0;height:751px;background:linear-gradient(160deg,#3a3a3c 0%,#8a8a8d 35%,#4a4a4d 60%,#2c2c2e 100%)}
.nav{top:44px;left:340px;display:flex;gap:36px;font-size:12px;font-weight:600;color:#fff}
.nav .active{color:var(--cyan)}
.hero-kicker{top:186px;left:58px;font-size:21px;color:#fff}
.hero-title{top:232px;left:56px;font-size:66px;line-height:70px;color:#fff;letter-spacing:-2px}
.hero-title .grad{background:var(--grad);-webkit-background-clip:text;background-clip:text;color:transparent}
.slide-ind{top:290px;left:1124px;width:24px;height:120px}
.hero-copy{top:523px;left:788px;width:365px;font-size:12px;line-height:18px;color:#fff}

/* welcome */
.welcome{top:751px;height:689px}
.welcome-copy{top:94px;left:648px;width:420px;font-size:14.5px;line-height:27px;color:#333}
.welcome-copy p+p{margin-top:27px}

/* panels */
.panels{top:1440px;height:694px}
.panel{position:absolute;top:0;height:694px;width:600px;color:#fff}
.panel-blue{left:0;background:linear-gradient(180deg,#5cb6fb,#45a7f8)}
.panel-purple{left:600px;background:linear-gradient(180deg,#a873f6,#a06bf4)}
.panel .ring{position:absolute;top:70px;width:126px;height:126px;border:3px solid #fff;border-radius:50%}
.panel h2{position:absolute;font-size:40px;line-height:42px;color:#fff}
.panel p{position:absolute;font-size:14.5px;line-height:27px}

/* ecosystem */
.eco{top:2134px;height:722px;background:var(--grey-bg)}
.eco h2{position:absolute;top:90px;width:100%;text-align:center;font-size:41px}
.eco .sub{position:absolute;top:154px;width:100%;text-align:center;font-size:14px;color:#333}
.card{position:absolute;top:222px;width:294px;height:317px;background:#fff;border-radius:8px;box-shadow:0 2px 10px rgba(0,0,0,.04)}
.card .num{position:absolute;top:22px;right:28px;font-size:40px;font-weight:400;color:#333}
.card .ico{position:absolute;top:46px;left:30px;width:64px;height:64px;border-radius:50%;background:linear-gradient(135deg,#46a8f8,#a46ef5)}
.card h3{position:absolute;top:140px;left:30px;font-size:16px;font-weight:600}
.card p{position:absolute;top:176px;left:30px;width:240px;font-size:13.5px;line-height:23px;color:#444}
.eco .note{position:absolute;top:592px;left:180px;width:840px;text-align:center;font-size:14.5px;line-height:27px;color:#333}

/* feature rows */
.feature{height:653px}
.feature h2{position:absolute;font-size:39px;line-height:42px}
.feature p{position:absolute;width:425px;font-size:14.5px;line-height:27px;color:#333}
.photo{position:absolute;border-radius:50%}

/* contact */
.contact{top:4100px;height:1154px;background:linear-gradient(180deg,#fff 0,#fff 255px,var(--navy) 255px)}
.contact-card{position:absolute;top:10px;left:133px;width:933px;height:592px;border-radius:10px;background:linear-gradient(160deg,#54b0fa 0%,#7a92f6 55%,#a673f4 100%)}
.contact-card h2{position:absolute;top:82px;width:100%;text-align:center;font-size:39px;color:#fff}
.contact-card .lead{position:absolute;top:134px;left:145px;width:643px;text-align:center;font-size:14.5px;line-height:24px;color:#fff}
.field{position:absolute;background:#fff;border-radius:6px;font-size:11px;color:#444;padding:16px 18px}
.submit{position:absolute;top:491px;left:377px;width:180px;height:40px;font-size:12px;background:linear-gradient(90deg,#2fa4f8,#57b4fb)}

/* footer */
.footer-brand{top:760px;left:122px;font-size:18px}
.footer-brand .brand-dot{width:40px;height:40px}
.socials{top:830px;left:123px;display:flex;gap:8px}
.socials span{width:33px;height:33px;border-radius:50%;background:#fff}
.f-col{position:absolute;top:690px;color:#fff}
.f-col h4{font-family:"Archivo",sans-serif;font-weight:900;font-size:14px;letter-spacing:-.3px;margin-bottom:24px}
.f-col ul{list-style:none;font-size:13px;line-height:30px}
.f-contact li{display:flex;gap:20px;margin-bottom:22px;font-size:13.5px;line-height:20px}
.f-ico{flex:0 0 40px;height:40px;border:1.5px solid #fff;border-radius:50%;display:flex;align-items:center;justify-content:center}
.f-rule{position:absolute;top:1000px;left:0;width:1200px;height:1px;background:#283049}
.copyright{position:absolute;top:1072px;width:100%;text-align:center;color:#fff;font-size:17px}
</style>
</head>
<body>

<section class="hero" role="img" aria-label="Black and white photograph looking up at tall glass skyscrapers against a cloudy sky">
  <div class="abs brand" style="top:38px;left:58px"><span class="brand-dot"></span><span>The Copper Lantern</span></div>
  <nav class="abs nav"><span class="active">Home</span><span>Framework</span><span>Projects</span><span>Halvemark</span><span>Insights</span><span>Company</span><span>Contact</span></nav>
  <a class="abs pill" style="top:35px;left:978px;width:163px;height:34px">Continue to Halvemark</a>

  <p class="abs hero-kicker">The Copper Lantern</p>
  <h1 class="abs display hero-title">Governance and<br><span class="grad">Project Origination</span><br>Framework</h1>

  <svg class="abs slide-ind" viewBox="0 0 24 120" fill="none" stroke="#fff" stroke-width="1.5">
    <path d="M12 2v26M6 8l6-6 6 6M12 92v26M6 112l6 6 6-6"/>
    <text x="15" y="44" transform="rotate(90 15 44)" fill="#fff" stroke="none" font-size="8" font-family="Inter,sans-serif">SLIDE 01</text>
  </svg>

  <p class="abs hero-copy">Published standards and oversight principles for structuring complex initiatives, with clear separation between governance, operations and project execution.</p>
  <a class="abs pill" style="top:610px;left:788px;width:202px;height:38px">Learn the Framework</a>
</section>

<section class="welcome">
  <h2 class="abs display" style="top:94px;left:135px;font-size:34px;line-height:44px;letter-spacing:-1px"><span class="c-blue">Welcome to</span><br>The Copper Lantern</h2>
  <div class="photo abs" style="top:215px;left:160px;width:360px;height:474px;border-radius:180px 180px 0 0;background:linear-gradient(180deg,#f3efe9,#d8c6b2)" role="img" aria-label="Photograph of a smiling woman holding a tablet"></div>
  <div class="abs welcome-copy">
    <p>The Copper Lantern is a governance and project origination group. Its purpose is to define structural standards and oversight principles for complex initiatives that may involve multiple parties, staged execution, and long-term accountability. This website publishes those standards and explains how responsibilities are separated across governance, operations, and project-level execution.</p>
    <p>This site is informational. It does not provide onboarding, account access, eligibility checks, custody of funds, escrow administration, or transaction execution. Where operational workflows exist, they are provided through a separate operating platform under separate terms and policies.</p>
  </div>
  <a class="abs pill" style="top:524px;left:648px;width:146px;height:40px">Learn More</a>
</section>

<section class="panels">
  <div class="panel panel-blue" role="img" aria-label="Blue tinted photograph of columned institutional building steps">
    <span class="ring" style="left:85px"></span>
    <h2 class="display" style="top:226px;left:85px">Governance<br>and Project<br>Origination</h2>
    <p style="top:376px;left:85px;width:420px">Governance in this context refers to the standards that determine how projects are structured and how oversight is described. Origination refers to the initial design and definition of an initiative, including role separation, reporting expectations, and boundary setting before execution begins. The Copper Lantern focuses on these governance-level elements rather than on operating day-to-day workflows.</p>
  </div>
  <div class="panel panel-purple" role="img" aria-label="Purple tinted photograph of a circuit board">
    <span class="ring" style="left:84px"></span>
    <h2 class="display" style="top:226px;left:84px">Clear Role<br>Separation</h2>
    <p style="top:334px;left:84px;width:425px">The ecosystem is designed around clear separation of responsibilities. Governance activities belong at the framework layer. Operational workflows, where available, belong on a separate operating platform designed for process execution and recordkeeping. Assets and project execution, where applicable, belong at the project level through ring-fenced structures created for specific initiatives. This separation is intended to reduce ambiguity and help stakeholders understand who is responsible for what</p>
  </div>
</section>

<section class="eco">
  <h2 class="display">How <span class="c-blue">the Ecosystem</span> Works</h2>
  <p class="sub">At a high level, the ecosystem can be understood as three layers:</p>
  <div class="card" style="left:135px"><span class="num">01</span><span class="ico"></span><h3>Governance</h3><p>Defines standards, explains role boundaries, and publishes framework information.</p></div>
  <div class="card" style="left:453px"><span class="num">02</span><span class="ico"></span><h3>Operations</h3><p>Manages workflow processes such as documentation steps and record-anchored audit events through a separate platform.</p></div>
  <div class="card" style="left:771px"><span class="num">03</span><span class="ico"></span><h3>Project execution</h3><p>occurs at the project level through dedicated structures that hold responsibilities and assets where applicable.</p></div>
  <p class="note">This website focuses on the governance layer and provides links to learn about structural concepts such as role separation, escrow and milestone framing, and recordkeeping terminology</p>
</section>

<section class="feature" style="top:2856px">
  <h2 class="display" style="top:160px;left:133px">Independent<br><span class="c-blue">Escrow and</span><br>Milestone<br><span class="c-purple">Oversight</span></h2>
  <p style="top:358px;left:133px">Some initiatives use independent escrow arrangements to coordinate staged releases linked to milestone completion. Escrow can support execution discipline by requiring defined evidence before releases occur. Escrow does not guarantee outcomes, timelines, or success, and it is not administered by this website operator. This site describes the concept for clarity and transparency</p>
  <div class="photo" style="top:160px;left:640px;width:424px;height:424px;background:linear-gradient(135deg,#e9e3dc,#b8aaa0)" role="img" aria-label="Photograph of a woman working thoughtfully at a laptop"></div>
</section>

<section class="feature" style="top:3509px">
  <div class="photo" style="top:60px;left:136px;width:424px;height:424px;background:linear-gradient(135deg,#1b2a44,#4a6a8c)" role="img" aria-label="Photograph of a woman pointing at data screens in an operations room"></div>
  <h2 class="display" style="top:88px;left:643px">Where<br><span class="c-blue">Operational</span><br>Workflows<br><span class="c-purple">Happen</span></h2>
  <p style="top:278px;left:643px">Operational workflows, including any onboarding or workflow participation where permitted, occur on a separate operating platform under separate terms and policies. If you need operational access, use the Halvemark page on this site to navigate externally. This website does not host those workflows.</p>
</section>

<section class="contact">
  <div class="contact-card">
    <h2 class="display">Contact and Inquiries</h2>
    <p class="lead">If you have questions about governance framework concepts, role boundaries, or information published on this website, you can contact the team using the Contact page. Do not submit sensitive personal data through public forms.</p>
    <div class="field" style="top:226px;left:161px;width:328px;height:46px">Your name</div>
    <div class="field" style="top:226px;left:504px;width:269px;height:46px">Phone</div>
    <div class="field" style="top:283px;left:161px;width:328px;height:47px">Email address</div>
    <div class="field" style="top:283px;left:504px;width:269px;height:47px">Subject</div>
    <div class="field" style="top:344px;left:161px;width:612px;height:117px">Message</div>
    <a class="pill submit">SUBMIT</a>
  </div>

  <div class="abs brand footer-brand"><span class="brand-dot"></span><span>The Copper Lantern</span></div>
  <div class="abs socials"><span></span><span></span><span></span><span></span></div>

  <div class="f-col f-contact" style="left:402px">
    <h4>CONTACT US</h4>
    <ul>
      <li><span class="f-ico"><svg width="16" height="18" viewBox="0 0 16 18" fill="none" stroke="#fff" stroke-width="1.5"><path d="M8 17s6-5.5 6-10A6 6 0 0 0 2 7c0 4.5 6 10 6 10z"/><circle cx="8" cy="7" r="2"/></svg></span><span>The Copper Lantern<br>18 Lantern Quay, Harbour<br>District</span></li>
      <li><span class="f-ico"><svg width="16" height="16" viewBox="0 0 16 16" fill="none" stroke="#fff" stroke-width="1.5"><path d="M3 1.5l3 3-1.5 2a9 9 0 0 0 5 5l2-1.5 3 3-2 2C6 14.5 1.5 10 1.5 3.5z"/></svg></span><span>Phone<br>+1 555-0142-7730</span></li>
      <li><span class="f-ico"><svg width="16" height="12" viewBox="0 0 16 12" fill="none" stroke="#fff" stroke-width="1.5"><rect x="1" y="1" width="14" height="10" rx="1"/><path d="M1 1l7 6 7-6"/></svg></span><span>Email<br>info@TheCopperLantern.example</span></li>
    </ul>
  </div>
  <div class="f-col" style="left:722px">
    <h4>QUICK LINKS</h4>
    <ul><li>Framework</li><li>Projects</li><li>Halvemark</li><li>Insights</li><li>Company</li><li>Contact</li><li>Glossary</li></ul>
  </div>
  <div class="f-col" style="left:902px">
    <h4>LEGAL</h4>
    <ul><li>Legal (Index)</li><li>Terms of Use</li><li>Privacy Policy</li><li>Cookie Policy</li><li>Disclaimer &amp; Risk Notices</li><li>Acceptable Use Policy</li><li>Accessibility Statement</li></ul>
  </div>
  <div class="f-rule"></div>
  <p class="copyright">Copyright © 2026 The Copper Lantern. All rights reserved.</p>
</section>

</body>
</html>
```